Exploding Software Company Needs a New Age Business Card Designed

We are in need of new business cards for our software company, Meridane Logic Works LLC, that specializes in web-based construction software. We have a software as a subscription called "Quarnelo" that is growing fast and we want business cards to be cutting edge like our software. We need to use our current logo and would like a QR code to scan. The tricky part to me is that we preach paperless with our software and electronic document management but still need business cards in today's market at times.
Updates

Need to have the QR code on the design. 

Add yellow or orange color to enhance the look.

Quarnelo is the key name but need to have the name of the company "Meridane Logic Works LLC" on the card too.

Target Market(s)

Our target market is the construction market that can range from people that are 20 to 65 years old. Most are men but more and more women are coming on.

Industry/Entity Type

Business

Requirements
Must have
• Must incorporate the logo for the software "Quarnelo". The logo is just the symbol. Change the Quarnelo word so it is easily legible.
Nice to have
• A "QR" code that can be scanned for the basic contact information such as company name, website, contact name, email and phone.

```html
<!DOCTYPE html>
<html lang="en">
<head>
<meta charset="utf-8">
<title>Quarnelo business card fronts</title>
<link href="https://fonts.googleapis.com/css2?family=Open+Sans:wght@400;600&display=swap" rel="stylesheet">
<style>
  :root {
    --backdrop: #8a4420;
    --card: #000000;
    --accent: #fff200;
    --steel: #aab1bb;
    --charcoal: #4a4a4a;
    --ink-light: #ffffff;
    --ink-muted: #9a9a9a;
    --ink-dark: #2b2b2b;
  }
  * { margin: 0; padding: 0; box-sizing: border-box; }
  html, body { width: 1200px; height: 857px; overflow: hidden; }
  body {
    background: var(--backdrop);
    font-family: "Open Sans", Arial, sans-serif;
    position: relative;
  }
  .variant-label {
    position: absolute;
    color: var(--ink-light);
    font-size: 50px;
    font-weight: 400;
    line-height: 1;
    width: 542px;
    text-align: center;
  }
  .card {
    position: absolute;
    width: 542px;
    height: 310px;
    background: var(--card);
    overflow: hidden;
  }
  .brand {
    position: absolute;
    left: 88px;
    top: 196px;
    display: flex;
    align-items: center;
    gap: 12px;
  }
  .brand-dot {
    width: 26px; height: 26px; border-radius: 50%;
    background: #c9ccd1;
  }
  .brand-name {
    color: var(--ink-light);
    font-size: 22px;
    font-weight: 600;
    letter-spacing: 4px;
  }
  .divider {
    position: absolute;
    left: 276px; top: 68px;
    width: 2px; height: 150px;
    background: linear-gradient(to bottom, transparent, #d8d8d8 50%, transparent);
  }
  .contact {
    position: absolute;
    left: 302px; top: 72px;
    color: var(--ink-light);
  }
  .person-name {
    color: var(--accent);
    font-size: 20px;
    font-weight: 600;
    line-height: 26px;
  }
  .person-title { font-size: 13.5px; line-height: 18px; }
  .card.muted-title .person-title { color: var(--ink-muted); }
  .contact-list { list-style: none; margin-top: 20px; }
  .contact-list li {
    display: flex; align-items: center; gap: 6px;
    font-size: 13.5px; line-height: 29px;
  }
  .contact-list svg { width: 13px; height: 13px; flex: none; }
  .band { position: absolute; left: 0; bottom: 0; width: 542px; height: 32px; }
  .company {
    position: absolute;
    font-size: 14px;
    font-weight: 600;
    color: var(--card);
  }
  .card.grey-band .company { color: var(--ink-dark); }
</style>
</head>
<body>

<div class="variant-label" style="left:37px;top:18px;">Front#1</div>
<div class="variant-label" style="left:635px;top:18px;">Front#2</div>
<div class="variant-label" style="left:37px;top:792px;">Front#5</div>
<div class="variant-label" style="left:630px;top:792px;">Front#6</div>

<!-- Variant 1 -->
<section class="card" style="left:37px;top:88px;">
  <div class="brand"><span class="brand-dot"></span><span class="brand-name">Quarnelo</span></div>
  <div class="divider"></div>
  <div class="contact">
    <p class="person-name">Your Name</p>
    <p class="person-title">Title</p>
    <ul class="contact-list">
      <li><svg viewBox="0 0 14 14"><circle cx="7" cy="7" r="6" fill="none" stroke="#fff200" stroke-width="1.4"/><path d="M5 4l1.5 1.5-1 1 2 2 1-1L10 9l-1 1.2C7 10 4 7 3.8 5z" fill="#fff200"/></svg>123-456-789</li>
      <li><svg viewBox="0 0 14 14"><rect x="1" y="4" width="12" height="8" fill="#fff200"/><path d="M1 4l6 4 6-4" fill="none" stroke="#000" stroke-width="1"/></svg>info@Quarnelo.com</li>
      <li><svg viewBox="0 0 14 14"><circle cx="7" cy="7" r="6" fill="none" stroke="#fff200" stroke-width="1.2"/><ellipse cx="7" cy="7" rx="2.6" ry="6" fill="none" stroke="#fff200" stroke-width="1"/><path d="M1 7h12M2 4h10M2 10h10" stroke="#fff200" stroke-width="0.9"/></svg>www.Quarnelo.com</li>
    </ul>
  </div>
  <svg class="band" viewBox="0 0 542 32"><polygon points="0,7 295,7 273,32 0,32" fill="var(--charcoal)"/><polygon points="299,7 542,7 542,32 277,32" fill="var(--accent)"/></svg>
  <span class="company" style="left:330px;top:288px;">Meridane Logic Works LLC</span>
</section>

<!-- Variant 2 -->
<section class="card" style="left:635px;top:88px;">
  <div class="brand"><span class="brand-dot"></span><span class="brand-name">Quarnelo</span></div>
  <div class="divider"></div>
  <div class="contact">
    <p class="person-name">Your Name</p>
    <p class="person-title">Title</p>
    <ul class="contact-list">
      <li><svg viewBox="0 0 14 14"><circle cx="7" cy="7" r="6" fill="none" stroke="#fff200" stroke-width="1.4"/><path d="M5 4l1.5 1.5-1 1 2 2 1-1L10 9l-1 1.2C7 10 4 7 3.8 5z" fill="#fff200"/></svg>123-456-789</li>
      <li><svg viewBox="0 0 14 14"><rect x="1" y="4" width="12" height="8" fill="#fff200"/><path d="M1 4l6 4 6-4" fill="none" stroke="#000" stroke-width="1"/></svg>info@Quarnelo.com</li>
      <li><svg viewBox="0 0 14 14"><circle cx="7" cy="7" r="6" fill="none" stroke="#fff200" stroke-width="1.2"/><ellipse cx="7" cy="7" rx="2.6" ry="6" fill="none" stroke="#fff200" stroke-width="1"/><path d="M1 7h12M2 4h10M2 10h10" stroke="#fff200" stroke-width="0.9"/></svg>www.Quarnelo.com</li>
    </ul>
  </div>
  <svg class="band" viewBox="0 0 542 32"><polygon points="0,7 295,7 273,32 0,32" fill="var(--charcoal)"/><polygon points="299,7 542,7 542,32 277,32" fill="var(--accent)"/></svg>
  <span class="company" style="left:330px;top:288px;">Meridane Logic Works LLC</span>
</section>

<!-- Variant 5 -->
<section class="card muted-title" style="left:37px;top:462px;">
  <div class="brand"><span class="brand-dot"></span><span class="brand-name">Quarnelo</span></div>
  <div class="divider"></div>
  <div class="contact">
    <p class="person-name">Your Name</p>
    <p class="person-title">Title</p>
    <ul class="contact-list">
      <li><svg viewBox="0 0 14 14"><circle cx="7" cy="7" r="6" fill="none" stroke="#fff200" stroke-width="1.4"/><path d="M5 4l1.5 1.5-1 1 2 2 1-1L10 9l-1 1.2C7 10 4 7 3.8 5z" fill="#fff200"/></svg>123-456-789</li>
      <li><svg viewBox="0 0 14 14"><rect x="1" y="4" width="12" height="8" fill="#fff200"/><path d="M1 4l6 4 6-4" fill="none" stroke="#000" stroke-width="1"/></svg>info@Quarnelo.com</li>
      <li><svg viewBox="0 0 14 14"><circle cx="7" cy="7" r="6" fill="none" stroke="#fff200" stroke-width="1.2"/><ellipse cx="7" cy="7" rx="2.6" ry="6" fill="none" stroke="#fff200" stroke-width="1"/><path d="M1 7h12M2 4h10M2 10h10" stroke="#fff200" stroke-width="0.9"/></svg>www.Quarnelo.com</li>
    </ul>
  </div>
  <svg class="band" viewBox="0 0 542 32"><polygon points="0,14 306,14 300,32 0,32" fill="var(--steel)"/><polygon points="323,0 542,0 542,32 303,32" fill="var(--accent)"/></svg>
  <span class="company" style="left:333px;top:285px;">Meridane Logic Works LLC</span>
</section>

<!-- Variant 6 -->
<section class="card muted-title grey-band" style="left:630px;top:462px;">
  <div class="brand"><span class="brand-dot"></span><span class="brand-name">Quarnelo</span></div>
  <div class="divider"></div>
  <div class="contact">
    <p class="person-name">Your Name</p>
    <p class="person-title">Title</p>
    <ul class="contact-list">
      <li><svg viewBox="0 0 14 14"><circle cx="7" cy="7" r="6" fill="none" stroke="#fff200" stroke-width="1.4"/><path d="M5 4l1.5 1.5-1 1 2 2 1-1L10 9l-1 1.2C7 10 4 7 3.8 5z" fill="#fff200"/></svg>123-456-789</li>
      <li><svg viewBox="0 0 14 14"><rect x="1" y="4" width="12" height="8" fill="#fff200"/><path d="M1 4l6 4 6-4" fill="none" stroke="#000" stroke-width="1"/></svg>info@Quarnelo.com</li>
      <li><svg viewBox="0 0 14 14"><circle cx="7" cy="7" r="6" fill="none" stroke="#fff200" stroke-width="1.2"/><ellipse cx="7" cy="7" rx="2.6" ry="6" fill="none" stroke="#fff200" stroke-width="1"/><path d="M1 7h12M2 4h10M2 10h10" stroke="#fff200" stroke-width="0.9"/></svg>www.Quarnelo.com</li>
    </ul>
  </div>
  <svg class="band" viewBox="0 0 542 32"><polygon points="0,14 305,14 298,32 0,32" fill="var(--accent)"/><polygon points="320,0 542,0 542,32 306,32" fill="var(--steel)"/></svg>
  <span class="company" style="left:334px;top:285px;">Meridane Logic Works LLC</span>
</section>

</body>
</html>
```